Marlowe Group needs a business card

I would like the card to be simple but modern and elegant.
I like black and white.
or black and gold.
we are a private finance lender and also are involved in property and property developments.

please look at the business card photos i provided i would like M.G only one one side and all the other details on the other side use fonts that tie in with my theme.

Industry/Entity Type

Finance

Contact Information for Business Card

Marlowe Group (M.G) Daniel Marlowe M: 0413586207 E: danmarl@inboxmail.test

Font styles to use
Other font styles liked:
• Use fonts that would reflect our business

Colors
000000
ffffff

Requirements
Must have
• one side of details
• other side has either M.G or Marlowe Group like in the photos provided

```html
<!DOCTYPE html>
<html lang="en">
<head>
<meta charset="utf-8">
<title>Marlowe Group — Business Card</title>
<link rel="stylesheet" href="https://fonts.googleapis.com/css2?family=Sorts+Mill+Goudy&display=swap">
<style>
  :root {
    --page: #ffffff;
    --card: #050505;
    --gold: #8b7851;
    --gold-text: #8a7753;
  }
  * { box-sizing: border-box; margin: 0; padding: 0; }
  html, body {
    width: 960px;
    height: 1200px;
    overflow: hidden;
    background: var(--page);
  }
  body {
    position: relative;
    font-family: "Sorts Mill Goudy", "Times New Roman", serif;
    color: var(--gold-text);
  }
  .card {
    position: absolute;
    left: 60px;
    width: 840px;
    height: 478px;
    background: var(--card);
  }
  .card--front { top: 70px; }
  .card--back { top: 652px; }

  /* double gold frame near the card edge */
  .frame {
    position: absolute;
    inset: 15px;
    border: 2px solid var(--gold);
  }
  .frame::after {
    content: "";
    position: absolute;
    inset: 3px;
    border: 1px solid var(--gold);
  }

  /* front side */
  .inner-panel {
    position: absolute;
    left: 102px;
    right: 100px;
    top: 70px;
    bottom: 71px;
    border: 1.5px solid var(--gold);
  }
  .title-rule {
    position: absolute;
    top: 232px;
    height: 8px;
    border-top: 1px solid var(--gold);
    border-bottom: 1px solid var(--gold);
  }
  .title-rule--left { left: 102px; width: 106px; }
  .title-rule--right { right: 100px; width: 112px; }
  .company-name {
    position: absolute;
    left: 0;
    right: 0;
    top: 213px;
    text-align: center;
    font-size: 36px;
    line-height: 1;
    letter-spacing: 0.2px;
    text-transform: uppercase;
  }

  /* back side */
  .monogram {
    position: absolute;
    left: 0;
    right: 0;
    top: 86px;
    text-align: center;
    font-size: 44px;
    line-height: 1;
  }
  .person-name {
    position: absolute;
    left: 0;
    right: 0;
    top: 196px;
    text-align: center;
    font-size: 40px;
    line-height: 1;
  }
  .name-rule {
    position: absolute;
    left: 258px;
    width: 322px;
    top: 247px;
    border-top: 2.5px solid var(--gold);
  }
  .contact-line {
    position: absolute;
    left: 0;
    right: 0;
    text-align: center;
    font-size: 35px;
    line-height: 1;
  }
  .contact-line--phone { top: 274px; }
  .contact-line--email { top: 345px; }
</style>
</head>
<body>

  <section class="card card--front" aria-label="Card front">
    <div class="frame"></div>
    <div class="inner-panel"></div>
    <div class="title-rule title-rule--left"></div>
    <div class="title-rule title-rule--right"></div>
    <h1 class="company-name">Marlowe Group</h1>
  </section>

  <section class="card card--back" aria-label="Card back">
    <div class="frame"></div>
    <p class="monogram">M.G</p>
    <h2 class="person-name">Daniel Marlowe</h2>
    <div class="name-rule"></div>
    <p class="contact-line contact-line--phone">M: 0413586207</p>
    <p class="contact-line contact-line--email">E: danmarl@inboxmail.test</p>
  </section>

</body>
</html>
```